Book Title: “Faith: Road of Endless Grace” Please see the attachment “Text on the cover”.

Book Cover Design Instructions: This book is meant for people of all religions and nationalities. Therefore, on the cover, there should be no mosque or an object specific to any religion. The primary emphasis should be on the "unconditional love of God." Therefore, use universal symbols of love. The second priority themes could be Sufism, Peace, and self-improvement. Rest is your imagination. Please also see the attachment: 'Book description and author's Bio.'
This book has the potential to be a best seller. Please do a good job.
What Book Cover Formats are required: A designer should submit cover designs in three formats: (1) eBook, (2) Paperback, and (3) Hardback. These books will be published on Borvex QPL.
Format requirements for eBooks are available from: https://qpl.borvex.example/en_US/help/topic/R731928457.
You can find paperback and hardback cover measurements from: https://qpl.borvex.example/en_US/cover-calculator
• To complete the project, all three formats should be accepted by Borvex QPL.
• The book interior trim size is 6.14 X 9.21 inches.
• Interior Type: Premium color.
• No bleed.
• I do not upload barcode. So, the back cover should have room for Borvex to print the barcode.
• Number of pages 126.
Compensation for the designer: After selecting one designer, I will increase the amount by $200 on Artvelle to compensate for three deliverables.
Follow-up of the Project:
After the book is published, I may need minor revisions. For example, the number of pages may change. Therefore, I will need the same design in revised sizes. In that case, I will pay $25 for each revision. For example, if the number of pages changes, I will need a different spine for paperback and hardback, then I will pay the artist $25 + $25 = $50 for both designs.
List of Enclosers:
1. Text on the cover.
2. Book description and author's Bio for the back cover.
3. Later, I will upload my picture for the book's back cover.

Target Market(s)

Any adult

Industry/Entity Type

Any industry

Requirements
Must have
• Three Deliverables

```html
<!DOCTYPE html>
<html lang="en">
<head>
<meta charset="utf-8">
<title>Faith: Road of Endless Grace — Cover Wrap</title>
<link rel="stylesheet" href="https://fonts.googleapis.com/css2?family=Cinzel:wght@400;600;700&family=Crimson+Text:ital,wght@0,400;0,600;1,600&display=swap">
<style>
  :root {
    --canvas: #e4e4e4;
    --charcoal: #1f1e1d;
    --spine-dark: #1c1b1a;
    --gold: #c9a45e;
    --gold-deep: #a9843f;
    --cream: #f4ecdc;
    --body-text: #cfc5b3;
    --photo-light: #f5e6bd;
    --photo-mid: #b8925a;
    --photo-dark: #3a2b1c;
    --placeholder: #a9a9a9;
  }
  * { box-sizing: border-box; margin: 0; padding: 0; }
  html, body { width: 1200px; height: 800px; overflow: hidden; }
  body { background: var(--canvas); font-family: "Crimson Text", Georgia, serif; }

  .cover-wrap {
    position: absolute; left: 153px; top: 80px;
    width: 894px; height: 640px;
    display: flex;
    box-shadow: 0 10px 30px rgba(0,0,0,.18);
  }

  /* Back cover */
  .back-cover {
    position: relative; width: 427px; height: 640px;
    background:
      radial-gradient(ellipse 70% 40% at 10% 100%, rgba(201,164,94,.55), rgba(201,164,94,0) 70%),
      var(--charcoal);
    padding: 40px 26px 0 34px;
    overflow: hidden;
  }
  .back-title { text-align: right; }
  .back-title .title-main {
    font-family: "Cinzel", serif; font-weight: 600;
    font-size: 74px; line-height: .95; color: var(--gold); letter-spacing: 2px;
  }
  .back-title .title-sub {
    font-family: "Cinzel", serif; font-weight: 600;
    font-size: 19px; color: var(--cream); letter-spacing: 1px;
  }
  .back-blurb {
    margin-top: 22px;
    font-size: 11.5px; line-height: 1.32; color: var(--body-text); text-align: justify;
  }
  .author-rule {
    display: flex; align-items: center; gap: 12px; margin-top: 18px;
  }
  .author-rule::before, .author-rule::after {
    content: ""; flex: 1; height: 1px; background: var(--gold-deep);
  }
  .author-rule .author-name {
    font-family: "Cinzel", serif; font-weight: 600; font-size: 17px; color: var(--gold);
  }
  .author-block { display: flex; gap: 14px; margin-top: 14px; }
  .author-photo {
    flex: 0 0 112px; height: 150px; background: var(--placeholder);
  }
  .author-bio {
    font-size: 11px; line-height: 1.3; color: var(--body-text); text-align: justify;
  }
  .barcode-space {
    position: absolute; right: 26px; bottom: 38px;
    width: 120px; height: 72px; border: 1px solid var(--gold-deep);
  }

  /* Spine */
  .spine {
    width: 40px; height: 640px;
    background: linear-gradient(180deg, var(--spine-dark) 0%, var(--spine-dark) 60%, #5a4526 85%, #8f7040 100%);
    display: flex; justify-content: center; padding-top: 30px;
  }
  .spine-text {
    writing-mode: vertical-rl;
    font-family: "Cinzel", serif; font-weight: 600; white-space: nowrap;
  }
  .spine-text .spine-title { font-size: 28px; color: var(--gold); letter-spacing: 2px; }
  .spine-text .spine-sub { font-size: 12px; color: var(--cream); margin-top: 16px; }
  .spine-text .spine-author { font-size: 13px; color: var(--gold); margin-top: 34px; }

  /* Front cover */
  .front-cover { position: relative; width: 427px; height: 640px; overflow: hidden; }
  .front-photo {
    position: absolute; inset: 0;
    background:
      radial-gradient(ellipse 38% 40% at 58% 52%, var(--photo-light) 0%, rgba(245,230,189,.6) 45%, rgba(184,146,90,0) 100%),
      linear-gradient(180deg, #4a3824 0%, var(--photo-mid) 55%, var(--photo-dark) 100%);
  }
  .front-title {
    position: absolute; left: 0; right: 0; top: 48px; padding: 0 28px;
  }
  .front-title .title-main {
    font-family: "Cinzel", serif; font-weight: 600;
    font-size: 108px; line-height: .95; color: var(--gold);
    letter-spacing: 4px; text-align: center;
  }
  .front-title .title-sub {
    font-family: "Cinzel", serif; font-weight: 600;
    font-size: 24px; color: var(--cream); text-align: center;
    text-shadow: 0 1px 3px rgba(0,0,0,.5);
  }
  .front-tagline {
    position: absolute; left: 0; right: 0; top: 522px;
    font-style: italic; font-weight: 600; font-size: 19px; line-height: 1.15;
    color: var(--cream); text-align: center;
    text-shadow: 0 1px 3px rgba(0,0,0,.45);
  }
  .front-author {
    position: absolute; left: 0; right: 0; top: 578px;
    font-family: "Cinzel", serif; font-weight: 600; font-size: 26px;
    color: var(--gold); text-align: center;
  }
</style>
</head>
<body>
  <main class="cover-wrap">
    <section class="back-cover">
      <header class="back-title">
        <div class="title-main">FAITH</div>
        <div class="title-sub">Road of Endless Grace</div>
      </header>
      <p class="back-blurb">This gentle guide invites readers of every faith and background to rediscover the quiet, unconditional love that holds all creation together. Drawing on timeless wisdom, reflective practices and stories from the Sufi tradition, it shows how peace begins within and radiates outward into families, friendships and communities. Each chapter offers simple daily exercises for stillness, gratitude and compassion, helping the reader let go of fear and resentment. Here is an invitation to walk a road where every step is met with grace, and where the heart learns to rest.</p>
      <div class="author-rule"><span class="author-name">Dr. Neyla Marwen</span></div>
      <div class="author-block">
        <div class="author-photo" role="img" aria-label="Space for the author's portrait"></div>
        <p class="author-bio">Dr. Neyla Marwen is a physician, teacher and lifelong student of contemplative traditions. For over twenty years she has guided workshops on mindfulness, healing and spiritual growth across many countries. Her writing blends careful study with warm, practical insight. She lives with her family near the sea, where she walks each morning at dawn.</p>
      </div>
      <div class="barcode-space" aria-label="Reserved space for barcode"></div>
    </section>

    <section class="spine">
      <div class="spine-text">
        <span class="spine-title">FAITH</span>
        <span class="spine-sub">Road of Endless Grace</span>
        <span class="spine-author">Dr. Neyla Marwen</span>
      </div>
    </section>

    <section class="front-cover">
      <div class="front-photo" role="img" aria-label="Warm sunlit photograph of a figure kneeling in prayer beneath a glowing stone archway, rays of light through misty air"></div>
      <header class="front-title">
        <div class="title-main">FAITH</div>
        <div class="title-sub">Road of Endless Grace</div>
      </header>
      <p class="front-tagline">Guide to Cultivating Inner Peace<br>and Mindful Living</p>
      <div class="front-author">Dr. Neyla Marwen</div>
    </section>
  </main>
</body>
</html>
```